New Zealand Marlborough Sauvignon Blanc wine packaging design

We need packaging design for our new wine brand, Dunmore Vale. The wine is a New Zealand Marlborough Sauvignon Blanc. We would like the packaging will portray elegance and style with an understated label. We are looking for a label that portrays the elegance of the French Riviera. The label should be round or pill shaped.
Updates

Industry/Entity Type

Wine

Font styles to use
Serif
Sans Serif

Requirements
Must have
• The words in order of importance: Dunmore Vale, Sauvignon Blanc, Marlborough, New Zealand. It should be fit to the bottle posted in the links
Nice to have
• a pill shape or circular shape
Should not have
• Illustrations of wine bottles, wine glasses, or grapes

```html
<!DOCTYPE html>
<html lang="en">
<head>
<meta charset="UTF-8">
<title>Dunmore Vale Sauvignon Blanc Label</title>
<link href="https://fonts.googleapis.com/css2?family=Cinzel:wght@400;500&family=Josefin+Sans:wght@300;700&display=swap" rel="stylesheet">
<style>
  :root {
    --canvas: #ffffff;
    --ink: #0b0b0b;
    --band-text: #ffffff;
    --wash-light: #f4f3c8;
    --wash-yellow: #e9ec9a;
    --wash-green: #c9d9a6;
    --wash-sage: #a9c0a0;
    --vine-light: #dfe8b8;
    --vine-mid: #9fbf7e;
    --vine-dark: #5f8a55;
  }
  * { margin: 0; padding: 0; box-sizing: border-box; }
  html, body {
    width: 1200px;
    height: 675px;
    overflow: hidden;
    background: var(--canvas);
  }
  .stage {
    position: relative;
    width: 1200px;
    height: 675px;
  }
  .label {
    position: absolute;
    left: 417px;
    top: 37px;
    width: 366px;
    height: 600px;
    border-radius: 183px;
    overflow: hidden;
    background: var(--wash-light);
  }
  .label__sky {
    position: absolute;
    left: 0; top: 0;
    width: 100%;
    height: 310px;
    background:
      radial-gradient(ellipse 60% 14% at 55% 48%, rgba(169,192,160,0.75), rgba(169,192,160,0) 100%),
      linear-gradient(180deg,
        var(--wash-green) 0%,
        var(--wash-light) 14%,
        var(--wash-yellow) 24%,
        var(--wash-light) 34%,
        #dfe6c8 52%,
        var(--wash-light) 64%,
        var(--wash-yellow) 80%,
        var(--wash-light) 100%);
  }
  .label__vineyard {
    position: absolute;
    left: 0; top: 343px;
    width: 100%;
    height: 257px;
    background:
      radial-gradient(circle at 38% 24%, #f3f1a8 0, rgba(243,241,168,0) 18%),
      linear-gradient(180deg, #fbfbf0 0%, var(--vine-light) 26%, var(--vine-mid) 62%, var(--vine-dark) 100%);
  }
  .label__region {
    position: absolute;
    top: 84px;
    width: 100%;
    text-align: center;
    font-family: "Josefin Sans", sans-serif;
    font-weight: 700;
    font-size: 10.5px;
    letter-spacing: 2.2px;
    color: var(--ink);
  }
  .label__brand {
    position: absolute;
    top: 168px;
    width: 100%;
    text-align: center;
    font-family: "Cinzel", serif;
    font-weight: 400;
    color: var(--ink);
    line-height: 52px;
  }
  .label__brand-line {
    display: block;
    font-size: 60px;
  }
  .label__varietal {
    position: absolute;
    left: 0; top: 310px;
    width: 100%;
    height: 33px;
    background: var(--ink);
    color: var(--band-text);
    font-family: "Josefin Sans", sans-serif;
    font-weight: 300;
    font-size: 20px;
    letter-spacing: 8.5px;
    text-align: center;
    line-height: 35px;
    padding-left: 8px;
  }
</style>
</head>
<body>
  <main class="stage">
    <section class="label">
      <div class="label__sky" role="img" aria-label="Soft yellow and sage watercolour sky with distant hills"></div>
      <div class="label__vineyard" role="img" aria-label="Ink and watercolour illustration of vineyard rows under a rising sun"></div>
      <p class="label__region">NEW ZEALAND · MARLBOROUGH</p>
      <h1 class="label__brand">
        <span class="label__brand-line">DUNMORE</span>
        <span class="label__brand-line">VALE</span>
      </h1>
      <p class="label__varietal">SAUVIGNON BLANC</p>
    </section>
  </main>
</body>
</html>
```